Website for new child psychology practice

New clinical psychology practice in NSW Australia, specialising in work with children, adolescents and families. I would like to feature the colours in the logo, which was recently designed by pixelharbor designer Odette.
I am seeking a professional looking page, which is easy to navigate and is colourful and playful but not childish.
Target Market(s)
Parents and professionals
Industry/Entity Type
Health
Coding
Coded - Design and coding required
Number of Pages Required
1 page
Font styles to use
Serif
Requirements
Must have
- Pages for 'About us' 'Services' 'Fees and information' 'Contact us'
Should not have
- Childish stock photos

```html
<!DOCTYPE html>
<html lang="en">
<head>
<meta charset="utf-8">
<title>Dr Clara Hollis – Clinical Psychologist</title>
<link href="https://fonts.googleapis.com/css2?family=Noto+Serif:wght@400;700&family=Roboto:ital,wght@0,400;0,500;0,700;1,400&display=swap" rel="stylesheet">
<style>
:root{
  --purple:#8e1f7e;
  --purple-dark:#6e1763;
  --orange:#e06a24;
  --red:#c0302a;
  --sand:#e7b774;
  --rust:#d0692e;
  --ink:#1e1e1e;
  --grey:#6b6b6b;
  --footer:#220607;
  --white:#ffffff;
}
*{margin:0;padding:0;box-sizing:border-box}
html,body{width:1200px;height:3662px;overflow:hidden}
body{position:relative;font-family:"Roboto",sans-serif;color:var(--ink);background:var(--white)}
.abs{position:absolute}
.serif{font-family:"Noto Serif",serif;font-weight:700}
.btn{position:absolute;display:flex;align-items:center;justify-content:center;gap:10px;border-radius:30px;background:linear-gradient(90deg,var(--purple-dark),var(--purple));color:#fff;font-weight:700;font-size:15px;letter-spacing:.2px}
.btn svg{width:15px;height:15px}
.photo{position:absolute}

/* header */
.topline{top:0;left:0;width:1200px;height:5px;background:var(--purple)}
.brand{display:flex;align-items:center;gap:10px;font-family:"Noto Serif",serif;font-size:24px;color:#5a2a4f;letter-spacing:.5px}
.brand .dot{width:34px;height:34px;border-radius:50%;background:var(--purple)}
.call{left:707px;top:24px;display:flex;align-items:center;gap:12px}
.call .ic{width:46px;height:46px;border-radius:50%;background:var(--orange);display:flex;align-items:center;justify-content:center}
.call small{display:block;font-size:15px;color:#444}
.call strong{font-size:17px;font-weight:700;color:#222}
.nav{left:438px;top:89px;display:flex;gap:22px;font-size:15px;color:#222;font-weight:500}
.nav .cur{color:var(--purple)}

/* hero */
.hero{top:145px;left:0;width:1200px;height:719px;background:linear-gradient(100deg,#c9c3bf 0%,#b7aaa0 35%,#6f6761 60%,#8a8580 100%)}
.hero h1{position:absolute;left:110px;top:345px;font-size:56px;color:#fff;line-height:1}
.hero h2{position:absolute;left:110px;top:418px;font-size:40px;color:#fff;line-height:1}
.hero p{position:absolute;left:111px;top:478px;width:520px;font-size:18px;line-height:26px;color:#fff;font-weight:500}

.pin{position:absolute;width:218px;height:250px}
.pin .label{position:absolute;left:0;width:218px;top:122px;text-align:center;color:#fff;font-weight:700;font-size:19px}
.pin .icon{position:absolute;left:69px;top:42px;width:80px;height:80px;border-radius:50%;background:rgba(0,0,0,.15);display:flex;align-items:center;justify-content:center}

/* services */
.sec-title{position:absolute;width:1200px;left:0;text-align:center;font-size:37px}
.card{position:absolute;top:1132px;width:307px;height:385px;background:#fff;border-radius:10px;box-shadow:0 2px 12px rgba(0,0,0,.18)}
.card .photo{left:6px;top:6px;width:295px;height:202px;border-radius:6px}
.card h3{position:absolute;top:230px;width:100%;text-align:center;font-size:19px;font-weight:500}
.card p{position:absolute;top:266px;left:20px;right:20px;text-align:center;font-size:14px;line-height:22px;color:var(--grey)}
.card .more{position:absolute;top:350px;width:100%;display:flex;justify-content:center;align-items:center;gap:6px;color:#e05a5a;font-weight:500;font-size:14px}

/* about */
.about{top:1629px;left:0;width:1200px;height:603px;background:linear-gradient(90deg,#e9be80,#e4b06b)}
.about .ring{position:absolute;left:121px;top:1701px;width:418px;height:418px;border-radius:50%;background:conic-gradient(var(--purple),var(--red),var(--purple));padding:6px}
.about .ring div{width:100%;height:100%;border-radius:50%;background:linear-gradient(135deg,#d9d2c6,#a79c8c)}
.about h2{position:absolute;left:599px;top:1726px;font-size:37px;line-height:42px;color:#fff}
.about p{position:absolute;left:599px;width:483px;font-size:15.5px;line-height:25.6px;color:#fff;text-align:justify}

/* fees */
.fees h2{position:absolute;left:110px;top:2348px;font-size:37px}
.fees p{position:absolute;left:110px;top:2399px;width:451px;font-size:15.5px;line-height:25.6px;color:var(--grey);text-align:justify}

/* testimonials */
.testi{top:2851px;left:0;width:1200px;height:402px;background:linear-gradient(90deg,#d8722f,#cf6229)}
.quote{position:absolute;top:2994px;width:300px;color:#fff}
.quote .mark{font-family:"Noto Serif",serif;font-size:56px;line-height:40px;font-weight:700}
.quote p{margin-top:12px;font-style:italic;font-size:13px;line-height:27px}
.quote .who{display:flex;align-items:center;gap:6px;margin-top:10px;font-size:13px}
.quote .av{width:38px;height:38px;border-radius:50%;background:#f3d2b4;border:2px solid #fff}
.quote .stars{color:#ffd34d;font-size:10px;letter-spacing:1px}

/* footer */
.footer{top:3253px;left:0;width:1200px;height:409px;background:var(--footer);color:#fff}
.fcol{position:absolute;top:3316px;font-size:14px}
.fcol h4{font-size:17px;font-weight:700;margin-bottom:22px}
.fcol li{list-style:none;height:37.7px}
.contact-item{display:flex;gap:12px;margin-bottom:16px}
.contact-item b{display:block;font-size:12px}
</style>
</head>
<body>

<div class="abs topline"></div>

<div class="abs brand" style="left:110px;top:78px"><span class="dot"></span>DR CLARA HOLLIS</div>

<div class="abs call">
  <div class="ic"><svg width="24" height="24" viewBox="0 0 24 24" fill="#fff"><path d="M6.6 10.8a15 15 0 006.6 6.6l2.2-2.2c.3-.3.7-.4 1-.2 1.1.4 2.3.6 3.6.6.6 0 1 .4 1 1V20c0 .6-.4 1-1 1A17 17 0 013 4c0-.6.4-1 1-1h3.5c.6 0 1 .4 1 1 0 1.3.2 2.5.6 3.6.1.3 0 .7-.2 1z"/></svg></div>
  <div><small>Call Us</small><strong>+1 555 010 2040</strong></div>
</div>

<div class="btn" style="left:941px;top:24px;width:145px;height:46px">LOGIN
  <svg viewBox="0 0 24 24" fill="#fff"><path d="M7 10V7a5 5 0 0110 0v3h1v11H6V10zm2 0h6V7a3 3 0 00-6 0z"/></svg></div>

<nav class="abs nav">
  <span class="cur">HOME</span><span>|</span><span>ABOUT US</span><span>|</span><span>SERVICES</span><span>|</span><span>FEES AND INFORMATION</span><span>|</span><span>CONTACT US</span>
</nav>

<section class="abs hero" role="img" aria-label="Photo of a psychologist taking notes while a man talks during a session">
</section>
<h1 class="abs serif" style="left:110px;top:345px;font-size:56px;color:#fff;line-height:1">DR.CLARA HOLLIS</h1>
<h2 class="abs serif" style="left:110px;top:418px;font-size:40px;color:#fff;line-height:1">CLINICAL PSYCHOLOGIST</h2>
<p class="abs" style="left:111px;top:478px;width:520px;font-size:18px;line-height:26px;color:#fff;font-weight:500">Lorem ipsum dolor sit consectetur adipiscing sed do eiusmod tempor incididunt ut labore et dolore magna aliquat</p>
<div class="btn" style="left:111px;top:554px;width:185px;height:47px">GET STARTED
  <svg viewBox="0 0 24 24"><circle cx="12" cy="12" r="10" fill="#fff"/><path d="M10 7l5 5-5 5" stroke="#8e1f7e" stroke-width="2.5" fill="none"/></svg></div>

<!-- audience pins -->
<div class="pin" style="left:272px;top:716px">
  <svg width="218" height="250" viewBox="0 0 218 250"><path d="M109 2a107 107 0 0175 183L109 250 34 185A107 107 0 01109 2z" fill="var(--orange)"/></svg>
  <div class="icon"><svg width="44" height="44" viewBox="0 0 24 24" fill="none" stroke="#fff" stroke-width="1.5"><circle cx="12" cy="7" r="4"/><path d="M4 21c0-4 4-7 8-7s8 3 8 7"/></svg></div>
  <div class="label">Children</div>
</div>
<div class="pin" style="left:490px;top:716px">
  <svg width="218" height="250" viewBox="0 0 218 250"><path d="M109 2a107 107 0 0175 183L109 250 34 185A107 107 0 01109 2z" fill="var(--purple)" stroke="#fff" stroke-width="4"/></svg>
  <div class="icon"><svg width="44" height="44" viewBox="0 0 24 24" fill="none" stroke="#fff" stroke-width="1.5"><circle cx="8" cy="7" r="3"/><circle cx="16" cy="7" r="3"/><path d="M3 20c0-4 2-7 5-7s5 3 5 7M11 20c0-4 2-7 5-7s5 3 5 7"/></svg></div>
  <div class="label">Adolescents</div>
</div>
<div class="pin" style="left:708px;top:716px">
  <svg width="218" height="250" viewBox="0 0 218 250"><path d="M109 2a107 107 0 0175 183L109 250 34 185A107 107 0 01109 2z" fill="var(--red)"/></svg>
  <div class="icon"><svg width="44" height="44" viewBox="0 0 24 24" fill="none" stroke="#fff" stroke-width="1.5"><circle cx="7" cy="6" r="3"/><circle cx="17" cy="6" r="3"/><circle cx="12" cy="13" r="2"/><path d="M2 21c0-5 2-9 5-9s5 4 5 9M12 21c0-5 2-9 5-9s5 4 5 9"/></svg></div>
  <div class="label">Families</div>
</div>

<!-- services -->
<h2 class="sec-title serif" style="top:1052px">OUR SERVICES</h2>

<div class="card" style="left:112px">
  <div class="photo" role="img" aria-label="Photo of a therapist talking with a young woman on a sofa" style="background:linear-gradient(135deg,#d8d4cf,#7d7975)"></div>
  <h3>Lorem ipsum dolor sit amet</h3>
  <p>Lorem ipsum dolor sit amet, consectetur adipiscing elited sed do eiusmod tempor incididunt labore dolore magna aliqua.</p>
  <div class="more">READ MORE <svg width="14" height="14" viewBox="0 0 24 24"><circle cx="12" cy="12" r="10" fill="#e05a5a"/><path d="M10 7l5 5-5 5" stroke="#fff" stroke-width="2.5" fill="none"/></svg></div>
</div>
<div class="card" style="left:446px">
  <div class="photo" role="img" aria-label="Photo of a psychologist in conversation with a boy" style="background:linear-gradient(135deg,#e4e1dc,#8a8580)"></div>
  <h3>Lorem ipsum dolor sit amet</h3>
  <p>Lorem ipsum dolor sit amet, consectetur adipiscing elited sed do eiusmod tempor incididunt labore dolore magna aliqua.</p>
  <div class="more">READ MORE <svg width="14" height="14" viewBox="0 0 24 24"><circle cx="12" cy="12" r="10" fill="#e05a5a"/><path d="M10 7l5 5-5 5" stroke="#fff" stroke-width="2.5" fill="none"/></svg></div>
</div>
<div class="card" style="left:781px">
  <div class="photo" role="img" aria-label="Photo of a couple in a counselling session" style="background:linear-gradient(135deg,#dcd7d1,#7b736b)"></div>
  <h3>Lorem ipsum dolor sit amet</h3>
  <p>Lorem ipsum dolor sit amet, consectetur adipiscing elited sed do eiusmod tempor incididunt labore dolore magna aliqua.</p>
  <div class="more">READ MORE <svg width="14" height="14" viewBox="0 0 24 24"><circle cx="12" cy="12" r="10" fill="#e05a5a"/><path d="M10 7l5 5-5 5" stroke="#fff" stroke-width="2.5" fill="none"/></svg></div>
</div>

<!-- about -->
<section class="abs about"></section>
<div class="about">
  <div class="ring"><div role="img" aria-label="Photo of a psychologist sitting with a young woman in chairs"></div></div>
  <h2 class="serif">ABOUT DR.CLARA<br>HOLLIS</h2>
  <p style="top:1817px">Lorem ipsum dolor sit amet, consectetur adipiscing elit, sed do eiusmod tempor incididunt ut labore et dolore magna aliqua. Ut enim ad minim veniam, quis nostrud exercitation ullamco laboris</p>
  <p style="top:1899px">Consectetur adipiscing elit, sed do eiusmod tempor incididunt ut labore et dolore magna aliqua. Ut enim ad minim veniam, quis nostrud exercitation ullamco laboris nisi ut aliquip ex ea commodo consequat. Duis aute irure dolor in reprehenderit in voluptate velit esse cillum dolore eu fugiat nulla pariatur. Excepteur sint occaecat cupidatat.</p>
</div>
<div class="btn" style="left:599px;top:2055px;width:160px;height:44px">LEARN MORE
  <svg viewBox="0 0 24 24"><circle cx="12" cy="12" r="10" fill="#fff"/><path d="M10 7l5 5-5 5" stroke="#8e1f7e" stroke-width="2.5" fill="none"/></svg></div>

<!-- fees -->
<div class="fees">
  <h2 class="serif">FEES AND INFORMATION</h2>
  <p>Lorem ipsum dolor sit amet consectetur adipiscing elit sed do eiusmod tempor incididunt ut labore eted dolore magna aliqua. Ut enim ad minim veniam, quis nostrud exercitation ullamco laboris nisi ut aliquip ex ea commodo consequat. Duis aute irure dolor in reprehenderit in voluptate velit esse cillum dolore eu fugiat nulla pariatur. Excepteur sint occaecat cupidatat non proident, sunt in culpa qui officia deserunt mollit anim unde omnis iste natus error sit voluptatem accusantium doloremque laudantium, totam rem aperiam, eaque ipsa quae ab illo inventore veritatis et quasi architecto beatae vitae dicta sunt explicabo.</p>
</div>
<div class="btn" style="left:110px;top:2674px;width:163px;height:45px">READ MORE
  <svg viewBox="0 0 24 24"><circle cx="12" cy="12" r="10" fill="#fff"/><path d="M10 7l5 5-5 5" stroke="#8e1f7e" stroke-width="2.5" fill="none"/></svg></div>

<svg class="abs" style="left:672px;top:2436px" width="42" height="78" viewBox="0 0 42 78" fill="var(--rust)">
  <circle cx="4" cy="4" r="2.5"/><circle cx="20" cy="4" r="2.5"/><circle cx="36" cy="4" r="2.5"/>
  <circle cx="4" cy="21" r="2.5"/><circle cx="20" cy="21" r="2.5"/><circle cx="36" cy="21" r="2.5"/>
  <circle cx="4" cy="38" r="2.5"/><circle cx="20" cy="38" r="2.5"/><circle cx="36" cy="38" r="2.5"/>
  <circle cx="4" cy="55" r="2.5"/><circle cx="20" cy="55" r="2.5"/><circle cx="36" cy="55" r="2.5"/>
  <circle cx="4" cy="72" r="2.5"/><circle cx="20" cy="72" r="2.5"/><circle cx="36" cy="72" r="2.5"/>
</svg>
<div class="abs" style="left:731px;top:2343px;width:370px;height:376px;background:var(--rust);border-radius:0 12px 12px 12px"></div>
<div class="photo" role="img" aria-label="Photo of a smiling couple sitting with a counsellor" style="left:720px;top:2332px;width:375px;height:374px;border-radius:0 12px 12px 12px;background:linear-gradient(135deg,#f1ebe4,#bfb3a6)"></div>
<div class="photo" role="img" aria-label="Photo of a girl drawing with a therapist" style="left:611px;top:2514px;width:259px;height:235px;border-radius:10px;border:4px solid #fff;box-shadow:0 3px 12px rgba(0,0,0,.25);background:linear-gradient(135deg,#ece7df,#b9aea3)"></div>

<!-- testimonials -->
<section class="abs testi"></section>
<h2 class="sec-title serif" style="top:2895px;color:#fff">OUR TESTIMONIALS</h2>

<div class="quote" style="left:112px">
  <div class="mark">“</div>
  <p>Lorem ipsum dolor sit amet, consectetur adipiscing elit, sed do eiusmod tempor incididunt ut labore et dolore magna aliqua.</p>
  <div class="who"><span class="av"></span><div>- MILO HARTEN<div class="stars">★★★★★</div></div></div>
</div>
<div class="quote" style="left:452px">
  <div class="mark">“</div>
  <p>Lorem ipsum dolor sit amet, consectetur adipiscing elit, sed do eiusmod tempor incididunt ut labore et dolore magna aliqua.</p>
  <div class="who"><span class="av"></span><div>- MILO HARTEN<div class="stars">★★★★★</div></div></div>
</div>
<div class="quote" style="left:792px">
  <div class="mark">“</div>
  <p>Lorem ipsum dolor sit amet, consectetur adipiscing elit, sed do eiusmod tempor incididunt ut labore et dolore magna aliqua.</p>
  <div class="who"><span class="av"></span><div>- MILO HARTEN<div class="stars">★★★★★</div></div></div>
</div>

<svg class="abs" style="left:570px;top:3194px" width="60" height="16" viewBox="0 0 60 16">
  <circle cx="8" cy="8" r="6" fill="#fff"/><circle cx="30" cy="8" r="6" fill="none" stroke="#fff" stroke-width="1.5"/><circle cx="52" cy="8" r="6" fill="none" stroke="#fff" stroke-width="1.5"/>
</svg>

<!-- footer -->
<footer class="abs footer"></footer>
<div class="abs brand" style="left:110px;top:3314px;color:#fff;font-size:22px"><span class="dot"></span>DR CLARA HOLLIS</div>

<div class="fcol" style="left:434px;color:#fff">
  <h4>Quick Links</h4>
  <ul><li>Home</li><li>About Us</li><li>Services</li><li>Fees and information</li><li>Contact Us</li></ul>
</div>
<div class="fcol" style="left:646px;color:#fff">
  <h4>About Company</h4>
  <ul><li>Terms of Use</li><li>Terms &amp; Condition</li><li>News</li><li>Privacy Policy</li><li>FAQ</li></ul>
</div>
<div class="fcol" style="left:870px;color:#fff">
  <h4>Contact Us</h4>
  <div class="contact-item"><svg width="12" height="16" viewBox="0 0 24 32" fill="var(--rust)"><path d="M12 0a12 12 0 00-12 12c0 9 12 20 12 20s12-11 12-20A12 12 0 0012 0zm0 17a5 5 0 110-10 5 5 0 010 10z"/></svg><div><b>Location</b>12 Wattle Grove Lane,<br>Orange NSW 2800</div></div>
  <div class="contact-item"><svg width="14" height="14" viewBox="0 0 24 24" fill="var(--rust)"><path d="M6.6 10.8a15 15 0 006.6 6.6l2.2-2.2c.3-.3.7-.4 1-.2 1.1.4 2.3.6 3.6.6.6 0 1 .4 1 1V20c0 .6-.4 1-1 1A17 17 0 013 4c0-.6.4-1 1-1h3.5c.6 0 1 .4 1 1 0 1.3.2 2.5.6 3.6.1.3 0 .7-.2 1z"/></svg><div><b>Phone</b>+1 555 010 2040</div></div>
  <div class="contact-item"><svg width="16" height="12" viewBox="0 0 24 18" fill="var(--purple)"><path d="M0 0h24v18H0zM2 2l10 8 10-8"/><path d="M2 2l10 8 10-8" stroke="#fff" stroke-width="2" fill="none"/></svg><div><b>Email</b>hello@claraholliscare.com</div></div>
</div>

<svg class="abs" style="left:1132px;top:3500px" width="36" height="36" viewBox="0 0 36 36"><circle cx="18" cy="18" r="18" fill="#c2519a"/><path d="M12 21l6-6 6 6" stroke="#fff" stroke-width="2.5" fill="none"/></svg>

<div class="abs" style="left:110px;top:3569px;width:978px;height:1px;background:rgba(255,255,255,.2)"></div>
<div class="abs" style="left:0;top:3598px;width:1200px;text-align:center;color:#fff;font-size:15px">2024 Copyright - Dr.Clara Hollis. | All Rights Reserved</div>

</body>
</html>
```